Foot doctor needs feet friendly business cards.

Business cards for Podiatrist. Needs to look professional and modern. Back side put an appointment card, and try to put a little basic street map somewhere on card along with all of our contact info below:

Marcus Dovan, DPM, Inc.
Diplomate, National Council of Lower Limb Medicine
Call: 1.877.Toes.482
1.555.283.9146
Fax: 1.555.671.3820
Email: info@DrDovanclinic.example
Web: www.DrDovanclinic.example
2847 W. Harbor Ln. Suite 204
Costa Mesa, CA 90000

```html
<!DOCTYPE html>
<html lang="en">
<head>
<meta charset="utf-8">
<title>Marcus Dovan, DPM – Business &amp; Appointment Cards</title>
<link rel="stylesheet" href="https://fonts.googleapis.com/css2?family=Open+Sans:ital,wght@0,400;0,600;0,700;1,600&display=swap">
<style>
  :root {
    --brand-blue: #2d5a86;
    --brand-blue-text: #2f5d8c;
    --ink: #1d1d1d;
    --paper: #ffffff;
    --backdrop: #ece9e4;
    --photo-light: #f1efec;
    --photo-skin: #d9a98a;
    --photo-shadow: #bfb6ae;
  }
  * { box-sizing: border-box; margin: 0; padding: 0; }
  html, body { width: 1200px; height: 900px; overflow: hidden; }
  body {
    background: var(--backdrop);
    font-family: "Open Sans", Arial, sans-serif;
    position: relative;
  }
  .card {
    position: absolute;
    width: 640px;
    height: 366px;
    background: var(--paper);
    box-shadow: 0 6px 18px rgba(0,0,0,0.18);
    overflow: hidden;
  }
  /* Appointment side */
  .appointment-card { left: 280px; top: 48px; padding: 34px 56px 0; }
  .appointment-title {
    text-align: center;
    color: var(--brand-blue-text);
    font-weight: 700;
    font-size: 17px;
    letter-spacing: 1px;
    margin-bottom: 20px;
  }
  .form-row {
    display: flex;
    align-items: flex-end;
    border-bottom: 1.5px solid var(--ink);
    height: 40px;
    font-size: 15px;
    color: var(--ink);
    padding-bottom: 3px;
  }
  .form-row .label { text-decoration: underline; }
  .form-row .label-time { margin-left: 220px; }
  .appointment-note {
    margin-top: 22px;
    text-align: center;
    color: var(--brand-blue-text);
    font-style: italic;
    font-weight: 600;
    font-size: 17px;
    line-height: 1.4;
  }
  /* Front side */
  .business-card { left: 280px; top: 470px; }
  .brand-band {
    position: absolute; left: 0; top: 0; right: 0; height: 212px;
    background: var(--brand-blue);
    color: var(--paper);
  }
  .identity { position: absolute; left: 40px; top: 62px; }
  .doctor-name { font-size: 25px; font-weight: 700; letter-spacing: 0.3px; line-height: 1.2; }
  .doctor-name .credentials { font-size: 19px; }
  .diplomate { font-size: 15.5px; line-height: 1.3; margin-top: 4px; width: 250px; }
  .address {
    position: absolute; left: 40px; top: 154px;
    font-size: 16.5px; line-height: 1.3;
  }
  .contact-list {
    position: absolute; right: 22px; top: 20px;
    list-style: none; text-align: right; font-size: 13px; line-height: 21px;
  }
  .contact-list li { display: flex; justify-content: flex-end; align-items: center; gap: 8px; }
  .contact-list svg { width: 12px; height: 12px; fill: var(--paper); stroke: var(--paper); }
  .feet-photo {
    position: absolute; left: 0; right: 0; top: 212px; bottom: 0;
    background: linear-gradient(180deg, var(--photo-light) 0%, var(--photo-skin) 60%, var(--photo-shadow) 100%);
  }
</style>
</head>
<body>

  <section class="card appointment-card" aria-label="Appointment card">
    <h2 class="appointment-title">APPOINTMENT</h2>
    <div class="form-row"><span class="label">For :</span><span class="label label-time">Time :</span></div>
    <div class="form-row"><span class="label">Date :</span></div>
    <div class="form-row"><span class="label">Location :</span></div>
    <div class="form-row"></div>
    <p class="appointment-note">If you are unable to keep appointment, please contact<br>us as soon as possible. Call&nbsp; 877 555 0142</p>
  </section>

  <section class="card business-card" aria-label="Business card">
    <div class="brand-band">
      <div class="identity">
        <h1 class="doctor-name">MARCUS DOVAN, <span class="credentials">DPM, INC.</span></h1>
        <p class="diplomate">Diplomate, National Council of Lower Limb Medicine</p>
      </div>
      <p class="address">2847 W. Harbor Ln. Suite 204<br>Costa Mesa, CA 90000</p>
      <ul class="contact-list">
        <li>1.877.Toes.482
          <svg viewBox="0 0 12 12"><path d="M1 4 Q6 0 11 4 L9 5 L8 3.5 Q6 3 4 3.5 L3 5 Z M2 6 H10 V10 H2 Z" stroke="none"/></svg></li>
        <li>1.555.283.9146
          <svg viewBox="0 0 12 12"><rect x="3" y="0.5" width="6" height="11" rx="1" stroke="none"/><rect x="4" y="2" width="4" height="6" fill="#2d5a86" stroke="none"/></svg></li>
        <li>1.555.671.3820
          <svg viewBox="0 0 12 12"><rect x="2" y="1" width="8" height="4" stroke="none"/><rect x="1" y="5" width="10" height="6" rx="1" stroke="none"/></svg></li>
        <li>info@DrDovanclinic.example
          <svg viewBox="0 0 12 12"><rect x="1" y="2.5" width="10" height="7" stroke="none"/><path d="M1 2.5 L6 6.5 L11 2.5" fill="none" stroke="#2d5a86" stroke-width="1"/></svg></li>
        <li>www.DrDovanclinic.example
          <svg viewBox="0 0 12 12"><path d="M4 8 L8 4 M5 3 L7 1 Q9 0 11 2 Q12 4 10 6 L9 7 M7 9 L5 11 Q3 12 1 10 Q0 8 2 6 L3 5" fill="none" stroke-width="1.4"/></svg></li>
      </ul>
    </div>
    <div class="feet-photo" role="img" aria-label="Photo of a family's bare feet sticking out from under white bed sheets"></div>
  </section>

</body>
</html>
```